Build Website for Playful Brand that helps content creators build businesses

Please help me create a website for my company that helps content creators build businesses around their audience. I have attached a design and vibe that I am going for at mossquay.io.

Open for changes, but I want to keep the colour I currently have (a light teal). Ultimately the brand is playful but should come off as a very modern elevated brand.

I am looking for a few pages including

1. Home (with clear CTA button)
A section where I can input what the company does, and some brands that we have launched

2. About Me
A simple page, that has preferably able to put a circular image of myself and then give a quick background about the company

3. Blog (can you include how blog posts will appear and it should sit nicely in the page)
This ideally is a section that will be able to link to another software so my blogs automatically flow into here or posts. But otherwise it should have sections of blocks where creators can see about topics that I post about

4. Contact (this should include a form that will allow users to contact me)
Finally a contact page where it links my socials, similar what is there, but ideally there is a form they can fill out which I can link to my inbox as well. This should be a simple page as well

Create a multi page website, including a page that will link or can link blog post

Similar to this vibe and logo - https://mossquay.io/

Target Market(s)

Content Creators

Coding

Coded - Design and coding required

Number of Pages Required

4 page

Requirements
Must have
• Home, Contact Me (Including a place to submit an enquiry and form), Blog Post Page As well

```html
<!DOCTYPE html>
<html lang="en">
<head>
<meta charset="utf-8">
<title>Moss Quay — Building Businesses</title>
<link rel="stylesheet" href="https://fonts.googleapis.com/css2?family=Mulish:wght@300;400;600;700;800&display=swap">
<style>
:root{
  --bg:#e4fbf8;
  --ink:#3c4e54;
  --ink-soft:#5b6b70;
  --line:#8a9a9e;
  --card:#ffffff;
  --photo-a:#9fb5b8;
  --photo-b:#5d6f72;
  --bear-a:#cfe6ee;
  --bear-b:#a9cfdc;
  --pattern-a:#d3ecea;
  --pattern-b:#7f9599;
}
*{box-sizing:border-box;margin:0;padding:0}
html,body{width:1200px;height:3278px;overflow:hidden;background:var(--bg);font-family:"Mulish",sans-serif;color:var(--ink)}
.page{position:relative;width:1200px;height:3278px;overflow:hidden}
.abs{position:absolute}
.btn{position:absolute;display:flex;align-items:center;justify-content:center;background:var(--ink);color:#fff;border-radius:26px;font-size:15px;font-weight:600;letter-spacing:.2px;text-decoration:none}
.brand-mark{display:flex;align-items:center;gap:10px;font-size:18px;letter-spacing:3px;color:var(--ink);font-weight:400}
.brand-mark .dot{width:22px;height:22px;border-radius:50%;border:2px solid var(--ink)}
.nav a{position:absolute;top:45px;font-size:16px;color:var(--ink);text-decoration:none}
.nav .active::after{content:"";position:absolute;left:-8px;right:-8px;top:26px;height:3px;background:var(--ink);border-radius:2px}
.hero-pattern{left:601px;top:137px;width:599px;height:349px;background:linear-gradient(120deg,var(--pattern-a) 0%,var(--pattern-b) 55%,var(--pattern-a) 100%);border-radius:4px}
.hero-title{left:112px;top:226px;font-size:52px;font-weight:700;letter-spacing:-.3px}
.hero-sub{left:113px;top:308px;font-size:18px}
.section-title{font-size:36px;font-weight:800;color:var(--ink)}
.section-title span{font-weight:300}
.rule{position:absolute;height:4px;background:var(--ink);border-radius:2px}
.photo{position:absolute;background:linear-gradient(135deg,var(--photo-a),var(--photo-b))}
.about-copy{left:667px;top:714px;width:420px;font-size:13px;line-height:25.7px;color:var(--ink-soft)}
.post{position:absolute;width:300px}
.post .date{display:flex;align-items:center;gap:6px;font-size:12px;color:var(--ink-soft)}
.post h3{margin-top:16px;font-size:17px;font-weight:400;line-height:26px;color:var(--ink)}
.post p{margin-top:14px;font-size:12.5px;line-height:24px;color:var(--ink-soft)}
.post a{display:inline-block;margin-top:12px;font-size:14px;font-weight:600;color:var(--ink);text-decoration:underline}
.brand-card{position:absolute;top:2087px;width:163px;height:146px;background:var(--card);border-radius:70px 70px 70px 20px;display:flex;align-items:center;justify-content:center;font-size:14px;font-weight:700;color:var(--ink);box-shadow:0 6px 18px rgba(60,78,84,.08)}
.field{position:absolute;border-bottom:1px solid var(--line);font-size:14px;color:var(--ink);padding:0 5px 16px}
.footer-nav a{position:absolute;top:3092px;font-size:14px;color:var(--ink);text-decoration:none;transform:translateX(-50%)}
.social{position:absolute;top:3140px;width:34px;height:34px;border-radius:50%;border:2px solid var(--ink)}
.copy{left:0;right:0;top:3205px;text-align:center;font-size:15px;color:var(--ink)}
</style>
</head>
<body>
<div class="page">

  <header>
    <div class="abs brand-mark" style="left:110px;top:78px"><span class="dot"></span>MOSS QUAY</div>
    <nav class="nav">
      <a class="active" href="https://mossquay.io/" style="left:689px">Home</a>
      <a href="#about" style="left:789px">About Me</a>
      <a href="#blog" style="left:912px">Blog</a>
      <a href="#contact" style="left:998px">Contact</a>
    </nav>
  </header>

  <section class="hero">
    <div class="abs hero-pattern" role="img" aria-label="Decorative zigzag stripe pattern in dark slate"></div>
    <h1 class="abs hero-title">Building Businesses</h1>
    <p class="abs hero-sub">Helping Content Creators Build Their Own Brand</p>
    <a class="btn" href="#about" style="left:114px;top:361px;width:122px;height:48px">ABOUT ME</a>
  </section>

  <section id="about">
    <svg class="abs" style="left:120px;top:578px" width="448" height="448" aria-hidden="true">
      <path d="M361.6 60.1 A214 214 0 1 1 304.2 25.6" fill="none" stroke="var(--ink)" stroke-width="10"/>
    </svg>
    <div class="photo" role="img" aria-label="Portrait of the founder writing notes at a desk beside a laptop" style="left:141px;top:599px;width:406px;height:406px;border-radius:50%"></div>
    <h2 class="abs section-title" style="left:667px;top:630px">ABOUT <span>ME</span></h2>
    <div class="rule" style="left:668px;top:682px;width:69px"></div>
    <p class="abs about-copy">Lorem ipsum dolor sit amet, consectetur adipiscing elit, sed do eiusmod tempor incididunt ut labore et dolore magna aliqua. Ut enim ad minim veniam, quis nostrud exercitation ullamco laboris nisi ut aliquip ex ea commodo consequat. Duis aute irure dolor in reprehenderit in voluptate velit esse cillum dolore eu fugiat nulla pariatur. Excepteur sint occaecat cupidatat non proident, sunt in culpa qui officia deserunt mollit anim id est laborum.</p>
    <a class="btn" href="#about" style="left:667px;top:918px;width:138px;height:48px">LEARN MORE</a>
  </section>

  <section id="blog">
    <h2 class="abs section-title" style="left:0;right:0;top:1146px;text-align:center">OUR BLOG <span>&nbsp;POST</span></h2>
    <div class="rule" style="left:565px;top:1198px;width:69px"></div>

    <div class="photo" role="img" aria-label="Hands typing on a laptop beside a coffee mug and notebook" style="left:111px;top:1248px;width:290px;height:262px;border-radius:6px"></div>
    <article class="post" style="left:442px;top:1282px">
      <div class="date"><svg width="14" height="14" viewBox="0 0 14 14"><rect x="1" y="2.5" width="12" height="10.5" fill="none" stroke="currentColor"/><line x1="1" y1="6" x2="13" y2="6" stroke="currentColor"/></svg>Aug 03,2024</div>
      <h3>Lorem ipsum dolor sit amet, consecte tur adipiscing elit, sed do eiusm</h3>
      <p>Sed ut perspiciatis unde omnis iste natus error sit voluptatem accusantium doloremque laudantium, totam rem aperiam, eaque ipsa quae ab illo</p>
      <a href="#blog">Read More</a>
    </article>
    <div class="photo" role="img" aria-label="Team of three discussing work around a laptop in an office" style="left:797px;top:1248px;width:290px;height:262px;border-radius:6px"></div>

    <div class="photo" role="img" aria-label="Person reading papers at a desk with a desktop monitor" style="left:111px;top:1549px;width:290px;height:262px;border-radius:6px"></div>
    <article class="post" style="left:442px;top:1582px">
      <div class="date"><svg width="14" height="14" viewBox="0 0 14 14"><rect x="1" y="2.5" width="12" height="10.5" fill="none" stroke="currentColor"/><line x1="1" y1="6" x2="13" y2="6" stroke="currentColor"/></svg>Aug 03,2024</div>
      <h3>Lorem ipsum dolor sit amet, consecte tur adipiscing elit, sed do eiusm</h3>
      <p>Sed ut perspiciatis unde omnis iste natus error sit voluptatem accusantium doloremque laudantium, totam rem aperiam, eaque ipsa quae ab illo</p>
      <a href="#blog">Read More</a>
    </article>
    <article class="post" style="left:794px;top:1565px">
      <div class="date"><svg width="14" height="14" viewBox="0 0 14 14"><rect x="1" y="2.5" width="12" height="10.5" fill="none" stroke="currentColor"/><line x1="1" y1="6" x2="13" y2="6" stroke="currentColor"/></svg>Aug 03,2024</div>
      <h3>Lorem ipsum dolor sit amet, consecte tur adipiscing elit, sed do eiusm</h3>
      <p>Sed ut perspiciatis unde omnis iste natus error sit voluptatem accusantium doloremque laudantium, totam rem aperiam, eaque ipsa quae ab illo</p>
      <a href="#blog">Read More</a>
    </article>

    <a class="btn" href="#blog" style="left:531px;top:1845px;width:138px;height:48px">VIEW MORE</a>
  </section>

  <section class="brands">
    <h2 class="abs section-title" style="left:0;right:0;top:1980px;text-align:center">OUR <span>BRANDS</span></h2>
    <div class="rule" style="left:565px;top:2032px;width:69px"></div>
    <div class="brand-card" style="left:118px">Northwick</div>
    <div class="brand-card" style="left:319px">Mintlay</div>
    <div class="brand-card" style="left:520px">Larkspur</div>
    <div class="brand-card" style="left:721px">Rowan Studio</div>
    <div class="brand-card" style="left:922px">Nightjar</div>
    <svg class="abs" style="left:558px;top:2272px" width="86" height="26" aria-label="Carousel controls">
      <circle cx="13" cy="13" r="12" fill="#9aa6a9"/><polyline points="16,7 10,13 16,19" fill="none" stroke="#fff" stroke-width="2.5"/>
      <circle cx="71" cy="13" r="12" fill="var(--ink)"/><polyline points="68,7 74,13 68,19" fill="none" stroke="#fff" stroke-width="2.5"/>
    </svg>
  </section>

  <section id="contact">
    <h2 class="abs section-title" style="left:113px;top:2420px">CONTACT <span>US</span></h2>
    <div class="rule" style="left:114px;top:2472px;width:69px"></div>
    <form>
      <div class="field" style="left:113px;top:2546px;width:251px">First Name :</div>
      <div class="field" style="left:384px;top:2546px;width:251px">Last Name :</div>
      <div class="field" style="left:113px;top:2613px;width:251px">Email :</div>
      <div class="field" style="left:384px;top:2613px;width:251px">Phone :</div>
      <div class="field" style="left:113px;top:2692px;width:522px">Message :</div>
      <button class="btn" type="submit" style="left:113px;top:2752px;width:152px;height:50px;border:0;font-family:inherit;font-size:16px">SUBMIT</button>
    </form>
    <div class="photo" role="img" aria-label="Illustration of a playful polar bear standing on a melting puddle" style="left:687px;top:2443px;width:446px;height:280px;border-radius:50% 50% 45% 45%;background:linear-gradient(160deg,var(--bear-a),var(--bear-b))"></div>
  </section>

  <footer>
    <div class="abs" style="left:111px;top:2894px;width:977px;height:2px;background:var(--ink)"></div>
    <div class="abs brand-mark" style="left:0;right:0;top:3015px;justify-content:center;font-size:20px"><span class="dot"></span>MOSS QUAY</div>
    <nav class="footer-nav">
      <a href="https://mossquay.io/" style="left:398px">HOME</a>
      <a href="#about" style="left:523px">ABOUT ME</a>
      <a href="#blog" style="left:646px">BLOG</a>
      <a href="#contact" style="left:777px">CONTACT US</a>
    </nav>
    <a class="social" href="#contact" aria-label="Photo sharing profile" style="left:549px"></a>
    <a class="social" href="#contact" aria-label="Professional network profile" style="left:592px"></a>
    <p class="abs copy">©Copyrights 2024 Mossquay &nbsp;|&nbsp;&nbsp; All Rights Reserved</p>
  </footer>

</div>
</body>
</html>
```